Kelvaro.ch is looking for business card letterhead and envelope C5 with WOW effect

We need a strong business card for our company Kelvaro.ch, logo is available. You want a black or dark background on which the logo Stark r% 26 # 252; appears. Letterhead and envelope in C5 format should be in a similar design, but does not have to be We need a strong business card for our company Kelvaro.ch, logo is available. A black or dark background is desired, on which the logo Stark comes across. The letterhead and the envelope in C5 format should have a similar design.

Target Market(s)

Private customers as well as entrepreneurs

Contact Information for Business Card

E-mail: info@kelvaro-example.ch
Web.www.Kelvaro-example.ch
Tel: +41 ( 0 ) 79 482 6037
Adresse:
Lindenweg 14
9406 Tarnbach

Hier kann man Icons verwenden für Email,Tel und Adressse

Font styles to use
Other font styles liked:
• Dubai,bold

Colors

Designer to choose colors to be used in the design.

Requirements
Must have
• WOW effect
Nice to have
• R% 26 # 252; back business card with our service listings. - VEHICLE LABELING - SHOP WINDOW LABELING - STICKERS AND MUCH MORE ... in red color

```html
<!DOCTYPE html>
<html lang="en">
<head>
<meta charset="utf-8">
<title>Kelvaro.ch business card</title>
<link rel="stylesheet" href="https://fonts.googleapis.com/css2?family=Exo+2:wght@500;800&family=Lato:wght@400&display=swap">
<style>
  :root {
    --backdrop: #7d7d7d;
    --brand-yellow: #f5c20b;
    --yellow-light: #ffd42a;
    --ink: #111111;
    --card-black: #050505;
    --white: #ffffff;
    --rule: #5a4a08;
  }
  html, body {
    margin: 0;
    width: 1200px;
    height: 1200px;
    overflow: hidden;
    background: var(--backdrop);
  }
  .canvas {
    position: relative;
    width: 1200px;
    height: 1200px;
  }
  .card {
    position: absolute;
    top: 310px;
    width: 366px;
    height: 595px;
    box-shadow: 2px 3px 6px rgba(0,0,0,.45);
    overflow: hidden;
  }
  .card-front {
    left: 233px;
    background: var(--brand-yellow);
    color: var(--ink);
    font-family: "Exo 2", sans-serif;
  }
  .card-back {
    left: 628px;
    width: 368px;
    background: var(--card-black);
  }
  .front-texture {
    position: absolute;
    inset: 0;
    background: radial-gradient(ellipse at 20% 60%, var(--yellow-light) 0%, rgba(255,212,42,0) 60%);
    opacity: .55;
  }
  .brand-name {
    position: absolute;
    left: 0;
    right: 0;
    margin: 0;
    text-align: center;
    font-family: "Exo 2", sans-serif;
    font-weight: 800;
    letter-spacing: 1px;
  }
  .card-front .brand-name {
    top: 428px;
    top: 122px;
    font-size: 44px;
    color: var(--ink);
  }
  .contact-icon {
    position: absolute;
    left: 0;
    width: 366px;
    height: 46px;
  }
  .contact-text {
    position: absolute;
    left: 0;
    right: 0;
    margin: 0;
    text-align: center;
    font-weight: 500;
    font-size: 20px;
    white-space: nowrap;
  }
  .contact-text.address { font-size: 21px; }
  .back-mark {
    position: absolute;
    left: 60px;
    top: 180px;
    width: 60px;
    height: 60px;
    border-radius: 50%;
    background: var(--brand-yellow);
  }
  .card-back .brand-name {
    top: 189px;
    left: 132px;
    right: auto;
    text-align: left;
    font-size: 30px;
    color: var(--white);
  }
  .service-list {
    position: absolute;
    top: 456px;
    left: 0;
    right: 0;
    margin: 0;
    padding: 0;
    list-style: none;
    text-align: center;
    font-family: "Lato", sans-serif;
    font-size: 17px;
    line-height: 27px;
    color: var(--brand-yellow);
  }
</style>
</head>
<body>
<div class="canvas">

  <section class="card card-front">
    <div class="front-texture" role="img" aria-label="Faint decorative background texture in lighter yellow"></div>
    <h1 class="brand-name">Kelvaro.ch</h1>

    <svg class="contact-icon" style="top:223px" viewBox="0 0 366 46" aria-hidden="true">
      <line x1="103" y1="23" x2="157" y2="23" stroke="var(--rule)" stroke-width="1"/>
      <line x1="209" y1="23" x2="263" y2="23" stroke="var(--rule)" stroke-width="1"/>
      <circle cx="183" cy="23" r="21" fill="var(--ink)"/>
      <path d="M176 14c2 0 3 3 3 4s-2 2-2 3c1 3 3 5 6 6 1 0 2-2 3-2s4 1 4 3-2 4-4 4c-8-1-13-6-14-14 0-2 2-4 4-4z" fill="var(--brand-yellow)"/>
    </svg>
    <p class="contact-text" style="top:278px">+41 ( 0 ) 79 482 6037</p>

    <svg class="contact-icon" style="top:313px" viewBox="0 0 366 46" aria-hidden="true">
      <line x1="103" y1="23" x2="157" y2="23" stroke="var(--rule)" stroke-width="1"/>
      <line x1="209" y1="23" x2="263" y2="23" stroke="var(--rule)" stroke-width="1"/>
      <circle cx="183" cy="23" r="21" fill="var(--ink)"/>
      <rect x="172" y="16" width="22" height="15" fill="var(--brand-yellow)"/>
      <path d="M172 16l11 8 11-8" fill="none" stroke="var(--ink)" stroke-width="1.5"/>
    </svg>
    <p class="contact-text" style="top:358px">info@kelvaro-example.ch</p>

    <svg class="contact-icon" style="top:388px" viewBox="0 0 366 46" aria-hidden="true">
      <line x1="103" y1="23" x2="157" y2="23" stroke="var(--rule)" stroke-width="1"/>
      <line x1="209" y1="23" x2="263" y2="23" stroke="var(--rule)" stroke-width="1"/>
      <circle cx="183" cy="23" r="21" fill="var(--ink)"/>
      <g fill="none" stroke="var(--brand-yellow)" stroke-width="1.6">
        <circle cx="183" cy="23" r="10"/>
        <ellipse cx="183" cy="23" rx="4.5" ry="10"/>
        <line x1="173" y1="23" x2="193" y2="23"/>
        <line x1="175" y1="17" x2="191" y2="17"/>
        <line x1="175" y1="29" x2="191" y2="29"/>
      </g>
    </svg>
    <p class="contact-text" style="top:438px">www.Kelvaro-example.ch</p>

    <svg class="contact-icon" style="top:470px" viewBox="0 0 366 46" aria-hidden="true">
      <line x1="103" y1="23" x2="157" y2="23" stroke="var(--rule)" stroke-width="1"/>
      <line x1="209" y1="23" x2="263" y2="23" stroke="var(--rule)" stroke-width="1"/>
      <circle cx="183" cy="23" r="21" fill="var(--ink)"/>
      <path d="M183 36c-5-6-9-11-9-16a9 9 0 0 1 18 0c0 5-4 10-9 16z" fill="var(--brand-yellow)"/>
      <circle cx="183" cy="20" r="3.5" fill="var(--ink)"/>
    </svg>
    <p class="contact-text address" style="top:523px">Lindenweg 14, 9406 Tarnbach</p>
  </section>

  <section class="card card-back">
    <span class="back-mark" aria-hidden="true"></span>
    <h2 class="brand-name">Kelvaro.ch</h2>
    <ul class="service-list">
      <li>VEHICLE LABELING</li>
      <li>SHOP WINDOW LABELING</li>
      <li>STICKERS AND MUCH MORE ...</li>
    </ul>
  </section>

</div>
</body>
</html>
```